Exclusive Crestline Groomers Invite that connects barbers

I am looking for a general invitation to join a secret club of people that shave their head. I want it the size of a business card that I can hand out to people I see on the street. I want it to feel like a special exclulisve invite to a club that only they can be apart of and want to tell their friends about.

Target Market(s)

35-60 male

Industry/Entity Type

Hair

Contact Information for Business Card

I want it to look like an invite to a secret club that only people that shave their head can be apart of... I will hand it out to people that I think fir our demographic.

Font styles to use
Serif

Colors

Designer to choose colors to be used in the design.

Requirements
Must have
• A feel of exclusivity
• website address (www.crestlinegroomers.example)
• logo

```html
<!DOCTYPE html>
<html lang="en">
<head>
<meta charset="utf-8">
<title>Crestline Groomers – Business Card</title>
<link href="https://fonts.googleapis.com/css2?family=Playfair+Display:wght@400;700&display=swap" rel="stylesheet">
<style>
  :root {
    --backdrop: #d6d6d6;
    --card-white: #ffffff;
    --card-black: #1e1e1e;
    --ink: #1c1c1c;
    --paper-text: #ffffff;
    --tan-light: #f3e2cf;
    --tan: #d9b994;
    --tan-deep: #c49a6c;
  }
  * { box-sizing: border-box; margin: 0; padding: 0; }
  html, body {
    width: 1200px; height: 800px; overflow: hidden;
    background: var(--backdrop);
    font-family: "Playfair Display", Georgia, serif;
  }
  .stage {
    width: 1200px; height: 800px;
    display: flex; align-items: center; justify-content: center; gap: 40px;
  }
  .card {
    width: 540px; height: 309px; position: relative; overflow: hidden;
    box-shadow: 0 6px 18px rgba(0,0,0,0.18);
  }

  /* Front face */
  .card-front { background: var(--card-white); color: var(--ink); }
  .brand-block {
    position: absolute; left: 30px; top: 0; width: 236px; height: 100%;
    display: flex; flex-direction: column; align-items: center; justify-content: center; gap: 16px;
  }
  .brand-square {
    width: 72px; height: 72px; border: 4px solid var(--ink); border-radius: 6px;
  }
  .brand-name {
    font-weight: 700; font-size: 20px; color: var(--ink); text-align: center; line-height: 1.2;
  }
  .divider {
    position: absolute; left: 280px; top: 82px; width: 1.5px; height: 142px; background: var(--ink);
  }
  .contact-block { position: absolute; left: 302px; top: 72px; }
  .person-name { font-weight: 700; font-size: 19px; letter-spacing: 1px; text-transform: uppercase; line-height: 1.2; }
  .person-title { font-size: 12px; margin-top: 2px; margin-bottom: 10px; letter-spacing: 0.5px; }
  .contact-list { list-style: none; font-size: 12px; line-height: 1.4; }
  .contact-list li { display: flex; align-items: flex-start; gap: 8px; white-space: nowrap; }
  .contact-list li.address { margin-bottom: 6px; }
  .contact-list svg { width: 10px; height: 10px; flex: none; margin-top: 4px; fill: var(--ink); }
  .accent-band {
    position: absolute; left: 57%; right: 0; bottom: 0; height: 10px;
    background: linear-gradient(90deg, var(--tan-deep), var(--tan-light) 45%, var(--tan) 100%);
  }

  /* Back face */
  .card-back {
    background: var(--card-black); color: var(--paper-text);
    display: flex; align-items: center; justify-content: center; gap: 20px;
  }
  .back-square {
    width: 62px; height: 62px; border: 4px solid var(--paper-text); border-radius: 6px;
  }
  .back-name { font-weight: 700; font-size: 34px; letter-spacing: 1px; }
</style>
</head>
<body>
<main class="stage">
  <section class="card card-front" aria-label="Business card front">
    <div class="brand-block">
      <div class="brand-square"></div>
      <div class="brand-name">Crestline Groomers</div>
    </div>
    <div class="divider"></div>
    <div class="contact-block">
      <h1 class="person-name">Marcus Ardley</h1>
      <p class="person-title">Founder</p>
      <ul class="contact-list">
        <li class="address">
          <svg viewBox="0 0 10 10"><path d="M5 0a3.5 3.5 0 0 0-3.5 3.5C1.5 6 5 10 5 10s3.5-4 3.5-6.5A3.5 3.5 0 0 0 5 0zm0 5a1.4 1.4 0 1 1 0-2.8A1.4 1.4 0 0 1 5 5z"/></svg>
          <span>48 Harlow Ave #12,<br>Ridgefield, CO 80000</span>
        </li>
        <li>
          <svg viewBox="0 0 10 10"><path d="M2.5 0h5a1 1 0 0 1 1 1v8a1 1 0 0 1-1 1h-5a1 1 0 0 1-1-1V1a1 1 0 0 1 1-1zm.5 1.5v6h4v-6z"/></svg>
          <span>555.010.4821</span>
        </li>
        <li>
          <svg viewBox="0 0 10 10"><path d="M2 0h6v3H2zM0 4h10v4H8v2H2V8H0zm3 3v2h4V7z"/></svg>
          <span>555-010-3390</span>
        </li>
        <li>
          <svg viewBox="0 0 10 10"><path d="M0 2h10v6H0zm1 1v.3L5 6l4-2.7V3L5 5.6z"/></svg>
          <span>info@crestlinegroomers.example</span>
        </li>
        <li>
          <svg viewBox="0 0 10 10"><path d="M5 0a5 5 0 1 0 0 10A5 5 0 0 0 5 0zm0 1c.6 0 1.3 1.4 1.5 3.5h-3C3.7 2.4 4.4 1 5 1zM1 5.5h1.6c0 1.3.3 2.5.7 3.2A4 4 0 0 1 1 5.5zm0-1a4 4 0 0 1 2.3-3.2c-.4.7-.7 1.9-.7 3.2zm4 4.5c-.6 0-1.3-1.4-1.5-3.5h3C6.3 7.6 5.6 9 5 9zm1.7-.3c.4-.7.7-1.9.7-3.2H9a4 4 0 0 1-2.3 3.2zM7.4 4.5c0-1.3-.3-2.5-.7-3.2A4 4 0 0 1 9 4.5z"/></svg>
          <span>www.crestlinegroomers.example</span>
        </li>
      </ul>
    </div>
    <div class="accent-band"></div>
  </section>

  <section class="card card-back" aria-label="Business card back">
    <div class="back-square"></div>
    <div class="back-name">Crestline Groomers</div>
  </section>
</main>
</body>
</html>
```